Business Card Design (NEW FILES)

ATTENTION: New vector files are available. Please update your design to reflect/use the new (better resolution) logo images.

Seeking a unique and professional business card design for a commercial drone photography/videography business. The layout should feature
the logo (attached) and include the following information:
Owen Tarrick
614-502-7738
www.skylarkreelworks.example
NRD Certified Remote Pilot

Owen Tarrick

```html
<!DOCTYPE html>
<html lang="en">
<head>
<meta charset="utf-8">
<title>Skylark Reelworks – Business Card</title>
<link rel="stylesheet" href="https://fonts.googleapis.com/css2?family=Open+Sans:wght@400;600;700&display=swap">
<style>
  :root {
    --backdrop: #222222;
    --card-white: #ffffff;
    --card-grey: #f3f3f3;
    --navy: #1b1b4f;
    --orange: #ec8a4a;
    --teal: #16b2b6;
    --ink: #1b1b4f;
  }
  html, body {
    margin: 0;
    padding: 0;
    width: 1200px;
    height: 780px;
    overflow: hidden;
    background: var(--backdrop);
    font-family: "Open Sans", Arial, sans-serif;
  }
  .stage {
    position: relative;
    width: 1200px;
    height: 780px;
  }
  .card {
    position: absolute;
    top: 236px;
    width: 540px;
    height: 309px;
    border-radius: 18px;
    overflow: hidden;
    box-shadow: 0 14px 30px rgba(0,0,0,0.45);
  }
  .card-front { left: 40px; background: var(--card-white); }
  .card-back  { left: 620px; background: var(--card-grey); }
  .card svg { display: block; }
  .wordmark { fill: var(--navy); font-weight: 600; }
  .contact { fill: var(--ink); font-size: 13px; font-weight: 400; }
  .name-first { fill: var(--orange); font-weight: 700; }
  .name-last { fill: var(--navy); font-weight: 700; }
  .role { fill: var(--navy); font-size: 13px; }
  .credential { fill: #ffffff; font-size: 13px; font-weight: 400; }
</style>
</head>
<body>
<main class="stage">

  <section class="card card-front" aria-label="Business card front">
    <svg width="540" height="309" viewBox="0 0 540 309">
      <g class="brand">
        <circle cx="44" cy="62" r="9" fill="var(--orange)"/>
        <text class="wordmark" x="62" y="71" font-size="26">Skylark Reelworks</text>
      </g>

      <g class="contact-block">
        <g class="icon-phone" fill="var(--orange)">
          <path d="M28 129 q-2 0 -2 3 q1 7 8 9 q3 0 3 -2 l0 -2 l-3 -1 l-1 1 q-3 -1 -4 -4 l1 -1 l-1 -3 z"/>
        </g>
        <text class="contact" x="44" y="141">614-502-7738</text>
        <g class="icon-globe" fill="none" stroke="var(--orange)" stroke-width="1.4">
          <circle cx="32" cy="159" r="6"/>
          <ellipse cx="32" cy="159" rx="2.6" ry="6"/>
          <line x1="26" y1="159" x2="38" y2="159"/>
        </g>
        <text class="contact" x="44" y="164">www.skylarkreelworks.example</text>
      </g>

      <g class="name-block">
        <text x="512" y="186" font-size="27" text-anchor="end">
          <tspan class="name-first">Owen </tspan><tspan class="name-last">Tarrick</tspan>
        </text>
        <text class="role" x="512" y="207" text-anchor="end">Owner</text>
        <rect class="edge-tab" x="528" y="214" width="12" height="48" fill="var(--orange)"/>
      </g>

      <g class="wave">
        <path d="M0 120 C8 190 70 232 190 240 C290 246 348 270 372 309 L0 309 Z" fill="var(--orange)"/>
        <path d="M0 120 C8 190 70 232 190 240 C250 244 300 250 330 270 C300 256 250 250 190 247 C80 242 14 205 0 150 Z" fill="#ffffff"/>
        <path d="M0 126 C6 190 60 232 170 240 C110 236 30 214 0 160 Z" fill="var(--teal)"/>
        <path d="M0 150 C8 205 60 238 150 244 C270 252 330 272 356 309 L0 309 Z" fill="var(--navy)"/>
        <path d="M0 136 C4 196 56 234 160 241 L150 244 C60 238 8 205 0 150 Z" fill="#ffffff"/>
      </g>

      <g class="credentials">
        <text class="credential" x="150" y="274" text-anchor="middle">NRD Certified Remote Pilot</text>
        <text class="credential" x="150" y="293" text-anchor="middle">Fully Insured</text>
      </g>
    </svg>
  </section>

  <section class="card card-back" aria-label="Business card back">
    <svg width="540" height="309" viewBox="0 0 540 309">
      <g class="brand">
        <circle cx="108" cy="154" r="13" fill="var(--orange)"/>
        <text class="wordmark" x="134" y="166" font-size="34">Skylark Reelworks</text>
      </g>
    </svg>
  </section>

</main>
</body>
</html>
```